Business Card Design

We provide services doing multiple jobs in the construction industry.Please note: The company name needs to be ROCK SOLID BUILDING SERVICESAttached logo was an example of what we wanted. Can you change up the colors?

Industry/Entity Type

Construction

Contact Information for Business Card

ROCK SOLID BUILDING SERVICES5401 HUDSON BEND RDAUSTIN, TX 78734(512)243-6854ROCKSOLIDBUILDINGSERVICES@GMAIL.COM

```html
<!DOCTYPE html>
<html lang="en">
<head>
<meta charset="utf-8">
<title>Pearlwood Framing Works – Business Card</title>
<link rel="stylesheet" href="https://fonts.googleapis.com/css2?family=Anton&family=Arimo:wght@400;700&display=swap">
<style>
  :root {
    --page-bg: #e9e7e3;
    --card-white: #ffffff;
    --band-black: #05080b;
    --brand-blue: #1b70a6;
    --logo-navy: #2a2f78;
    --stone-grey: #9a9a9a;
    --text-white: #ffffff;
  }
  html, body {
    margin: 0;
    width: 1200px;
    height: 800px;
    overflow: hidden;
    background: var(--page-bg);
  }
  .card {
    position: absolute;
    left: 75px;
    top: 100px;
    width: 1050px;
    height: 600px;
    background: var(--card-white);
    box-shadow: 0 12px 30px rgba(0,0,0,.18);
    overflow: hidden;
  }
  .card-shapes { position: absolute; inset: 0; }
  .brand-mark {
    position: absolute;
    left: 70px;
    top: 95px;
    display: flex;
    align-items: center;
    gap: 16px;
    font-family: "Anton", sans-serif;
    font-size: 44px;
    letter-spacing: 1px;
    color: var(--logo-navy);
  }
  .brand-mark .mark-square {
    width: 40px;
    height: 40px;
    background: var(--logo-navy);
  }
  .contact-list {
    position: absolute;
    left: 60px;
    top: 320px;
    margin: 0;
    padding: 0;
    list-style: none;
    font-family: "Arimo", sans-serif;
    font-size: 21px;
    color: var(--text-white);
    letter-spacing: .3px;
  }
  .contact-list li {
    display: flex;
    align-items: center;
    gap: 16px;
    height: 40px;
  }
  .contact-list svg { width: 22px; height: 22px; fill: var(--text-white); flex: none; }
  .name-block {
    position: absolute;
    left: 740px;
    top: 395px;
    color: var(--text-white);
  }
  .name-block .name-main {
    font-family: "Anton", sans-serif;
    font-size: 58px;
    line-height: 1;
    letter-spacing: 1px;
  }
  .name-block .name-sub {
    font-family: "Arimo", sans-serif;
    font-size: 22px;
    letter-spacing: 1px;
    margin-top: 6px;
  }
</style>
</head>
<body>
  <div class="card">
    <svg class="card-shapes" viewBox="0 0 1050 600" width="1050" height="600">
      <defs>
        <linearGradient id="stoneFill" x1="0" y1="0" x2="1" y2="1">
          <stop offset="0" stop-color="#a8a8a8"/>
          <stop offset="1" stop-color="#8c8c8c"/>
        </linearGradient>
      </defs>
      <polygon class="contact-band" points="0,250 650,250 682,560 0,560" fill="var(--band-black)"/>
      <polygon class="name-panel" points="662,322 1050,322 1050,560 694,560" fill="var(--brand-blue)"/>
      <rect class="mountain-art" x="690" y="110" width="320" height="180" rx="6" fill="url(#stoneFill)" opacity=".7" role="img" aria-label="Grey mountain ridge illustration"/>
    </svg>

    <div class="brand-mark"><span class="mark-square"></span>PEARLWOOD FRAMING WORKS</div>

    <ul class="contact-list">
      <li>
        <svg viewBox="0 0 24 24" aria-hidden="true"><path d="M6.6 10.8a15 15 0 0 0 6.6 6.6l2.2-2.2c.3-.3.7-.4 1-.2 1.1.4 2.3.6 3.6.6.6 0 1 .4 1 1V20c0 .6-.4 1-1 1A17 17 0 0 1 3 4c0-.6.4-1 1-1h3.5c.6 0 1 .4 1 1 0 1.3.2 2.5.6 3.6.1.3 0 .7-.2 1z"/></svg>
        (512)555-0193
      </li>
      <li>
        <svg viewBox="0 0 24 24" aria-hidden="true"><path d="M12 3 2 12h3v9h5v-6h4v6h5v-9h3z"/></svg>
        7732 FERNGLEN PASS LN AUSTIN, TX 78734
      </li>
      <li>
        <svg viewBox="0 0 24 24" aria-hidden="true"><path d="M2 5h20v14H2zm2 2v.5l8 5 8-5V7zm0 2.8V17h16V9.8l-8 5z"/></svg>
        PEARLWOODFRAMINGWORKS@MAILNEST.EXAMPLE
      </li>
    </ul>

    <div class="name-block">
      <div class="name-main">PEARLWOOD</div>
      <div class="name-sub">FRAMING WORKS</div>
    </div>
  </div>
</body>
</html>
```